Web Design Project

This is a wordpress project for a newly formed biologics company based in the US with international clientele. We do manufacturing of biologically based raw materials using a state of the art facility....Our logo must be incorporated....logo colors Navy and Gray. It is fine to use some color in web design. The viewer will primarily be industry folk.

Torvell Biologics, LLC is a contract manufacturing organization which produces biologically-based raw materials derived primarily from human plasma. The company services include extraction and purification of plasma components, especially proteins and enzymes. The business focuses on biotherapeutics, diagnostic and veterinary markets worldwide.

5 pages a bad example of first page can be found in attached files.....
use stock photos of labs and clean rooms.
Updates

Project Deadline Extended
Reason: I need a bit more time tonprovide feedback.

Project Deadline Extended
Reason: needed time to evaluate existing options

Target Market(s)

target market Pharmaceutical companies and research universities

Industry/Entity Type

Veterinary

Requirements
Must have
• our logo...we will provide some graphics...

```html
<!DOCTYPE html>
<html lang="en">
<head>
<meta charset="utf-8">
<title>Torvell Biologics – Team</title>
<link rel="stylesheet" href="https://fonts.googleapis.com/css2?family=PT+Sans+Narrow:wght@400;700&family=Open+Sans:wght@400;600;700&display=swap">
<style>
:root{
  --navy:#0b2f5e;
  --navy-deep:#04214a;
  --footer:#06234b;
  --banner:#0a4587;
  --cyan:#4fd3e0;
  --gray-bar:#b0b0b0;
  --text-navy:#102a55;
  --link-light:#a9bbd2;
  --link-dim:#47699a;
  --rule:#9aa3ad;
  --white:#ffffff;
}
*{box-sizing:border-box;margin:0;padding:0}
html,body{width:1168px;height:1200px;overflow:hidden}
body{position:relative;font-family:"PT Sans Narrow",Arial,sans-serif;color:var(--text-navy);
  background:linear-gradient(#ececec 0,#e2e2e2 420px,#c9c9c9 820px,#8f8f8f 925px)}
.abs{position:absolute}

.site-header{left:0;top:0;width:1168px;height:86px;
  background:linear-gradient(#fbfbfb,#d3d3d3);border-bottom:2px solid var(--cyan)}
.brand{left:54px;top:14px;display:flex;align-items:center;gap:10px}
.brand-dot{width:56px;height:56px;border-radius:50%;background:var(--navy)}
.brand-name{font-family:"Open Sans",Arial,sans-serif;font-weight:700;font-size:21px;color:var(--navy)}
.main-nav{left:0;top:24px;width:1168px;height:40px}
.main-nav a{position:absolute;top:0;height:40px;line-height:38px;font-family:"Open Sans",Arial,sans-serif;
  font-size:22px;font-weight:600;color:var(--white);text-decoration:none;text-shadow:0 1px 3px #555}
.main-nav a.active{border:2px solid #8fa0b0;border-radius:9px;background:linear-gradient(#d7dde3,#aeb7c1);padding:0 14px}

.banner{left:30px;top:88px;width:1098px;height:246px;overflow:hidden;
  background:linear-gradient(100deg,#0a3c78,#0e5aa6 45%,#0a3f7d)}
.banner-base{left:0;top:205px;width:1098px;height:41px;background:linear-gradient(#1d6ac2,#0c3f7c)}
.slide{border:3px solid #cfd8e2}
.slide-side{background:linear-gradient(90deg,#9fb3c7,#e9f0f6)}
.slide-main{background:linear-gradient(#dfe9f3,#b7cde2 70%,#2d6fb8)}
.dot{width:22px;height:22px;border-radius:50%;background:#2a67a8;color:#fff;font:600 14px/22px "Open Sans",Arial,sans-serif;text-align:center}
.dot.current{background:#0c1f3c}

.section-bar{left:46px;top:354px;width:1050px;height:48px;background:var(--gray-bar);border-bottom:2px solid var(--cyan)}
.section-title{left:24px;top:4px;font-size:32px;font-weight:700;color:#fff;text-shadow:0 1px 3px #666}
.search-box{left:826px;top:7px;width:206px;height:28px;background:#fff;border:1px solid #999;font:11px/26px "Open Sans",Arial,sans-serif;color:#888;padding-left:10px}
.search-btn{right:0;top:0;width:26px;height:26px;background:#e4e4e4;border-left:1px solid #aaa}

.group-title{left:629px;top:408px;font-size:27px;font-weight:700;color:var(--navy)}
.member-photo{width:133px;height:172px;border:1px solid var(--navy);background:linear-gradient(135deg,#2f8d9c,#8cd0d6 55%,#dff1f2)}
.member{width:278px}
.member-name{font-size:23px;font-weight:700;line-height:28px}
.member-role{font-size:20px;font-weight:700;font-style:italic;line-height:26px}
.member-bio{font-size:19px;line-height:26.5px;text-align:justify}
.divider{height:16px;color:var(--rule);font-size:18px;line-height:16px}
.divider span{display:inline-block;width:410px;border-top:2px dashed var(--rule);vertical-align:middle;margin-right:8px}

.site-footer{left:0;top:925px;width:1168px;height:275px;background:var(--footer)}
.foot-col{top:62px;font-family:"Open Sans",Arial,sans-serif;font-size:20px;line-height:26.5px}
.foot-col.primary{color:var(--link-light)}
.foot-col.quick{color:var(--link-dim)}
.foot-rule{top:30px;width:1px;height:175px;background:#17386a}
.follow{left:956px;top:50px;font:20px "Open Sans",Arial,sans-serif;color:var(--link-dim)}
.social{top:85px;width:28px;height:28px;background:#3a78c2;border-radius:3px}
.foot-search{left:952px;top:138px;width:156px;height:28px;background:#12407d;border:1px solid #3c6aa5;
  font:600 14px/26px "Open Sans",Arial,sans-serif;color:#fff;padding-left:10px}
.foot-search i{position:absolute;right:0;top:0;width:20px;height:26px;background:#6f88a8}
.copyright{left:0;top:232px;width:1168px;text-align:center;font:13px "Open Sans",Arial,sans-serif;color:#28497a}
</style>
</head>
<body>

<header class="site-header abs">
  <div class="brand abs"><span class="brand-dot"></span><span class="brand-name">Torvell Biologics</span></div>
  <nav class="main-nav abs">
    <a style="left:511px">Home</a>
    <a style="left:608px">Facilities</a>
    <a class="active" style="left:719px">Team</a>
    <a style="left:824px">Announcements</a>
    <a style="left:1036px">Contact</a>
  </nav>
</header>

<section class="banner abs">
  <div class="banner-base abs"></div>
  <div class="slide slide-side abs" role="img" aria-label="Laboratory workstation photo" style="left:240px;top:32px;width:160px;height:190px"></div>
  <div class="slide slide-side abs" role="img" aria-label="Clean room corridor photo" style="left:728px;top:32px;width:220px;height:190px;background:linear-gradient(90deg,#e6eef5,#a8bed3)"></div>
  <div class="slide slide-main abs" role="img" aria-label="Clean room laboratory photo" style="left:394px;top:10px;width:334px;height:224px"></div>
  <div class="dot abs" style="left:500px;top:214px">1</div>
  <div class="dot abs" style="left:530px;top:214px">2</div>
  <div class="dot current abs" style="left:561px;top:214px">3</div>
  <div class="dot abs" style="left:592px;top:214px">4</div>
</section>

<div class="section-bar abs">
  <h1 class="section-title abs">Team</h1>
  <div class="search-box abs">Search
    <span class="search-btn abs"><svg width="26" height="26" viewBox="0 0 26 26"><circle cx="12" cy="11" r="5" fill="none" stroke="#777" stroke-width="1.6"/><line x1="15.5" y1="14.5" x2="19" y2="18" stroke="#777" stroke-width="1.8"/></svg></span>
  </div>
</div>

<h2 class="group-title abs">Management:</h2>

<div class="member-photo abs" role="img" aria-label="Portrait photo of team member" style="left:86px;top:456px"></div>
<div class="member abs" style="left:249px;top:458px">
  <p class="member-name">Dana Whitcombe</p>
  <p class="member-bio">Lorem ipsum dolor sit amet, consectetuer adipiscing elit, sed diam nonummy nibh euismod tincidunt ut laoreet dolore magna aliquam erat volutpat.</p>
</div>

<div class="member-photo abs" role="img" aria-label="Portrait photo of team member" style="left:629px;top:456px"></div>
<div class="member abs" style="left:793px;top:458px">
  <p class="member-name">Dana Whitcombe</p>
  <p class="member-role">President and Chief Executive Officer</p>
  <p class="member-bio">Lorem ipsum dolor sit amet, consectetuer adipiscing elit, sed diam nonummy nibh euismod tincidunt ut laoreet dolore magna aliquam erat volutpat.</p>
</div>

<div class="divider abs" style="left:90px;top:654px"><span></span>&gt;&gt;</div>
<div class="divider abs" style="left:629px;top:654px"><span></span>&gt;&gt;</div>

<div class="member-photo abs" role="img" aria-label="Portrait photo of team member" style="left:86px;top:691px"></div>
<div class="member abs" style="left:249px;top:697px">
  <p class="member-name">Lena Marchetti</p>
  <p class="member-bio">Lorem ipsum dolor sit amet, consectetuer adipiscing elit, sed diam nonummy nibh euismod tincidunt ut laoreet dolore magna aliquam erat volutpat.</p>
</div>

<div class="member-photo abs" role="img" aria-label="Portrait photo of team member" style="left:629px;top:691px"></div>
<div class="member abs" style="left:793px;top:697px">
  <p class="member-name">Owen Rackley</p>
  <p class="member-role">Chief Operation Officer</p>
  <p class="member-bio">Lorem ipsum dolor sit amet, consectetuer adipiscing elit, sed diam nonummy nibh euismod tincidunt ut laoreet dolore magna aliquam erat volutpat.</p>
</div>

<footer class="site-footer abs">
  <div class="foot-col primary abs" style="left:74px">Home<br>Facilities<br>Team<br>Links<br>Contact</div>
  <div class="foot-rule abs" style="left:215px"></div>
  <div class="foot-col quick abs" style="left:260px">Some Quick Links<br>Some Quick Links<br>Some Quick Links<br>Some Quick Links<br>Some Quick Links</div>
  <div class="foot-rule abs" style="left:464px"></div>
  <div class="foot-col quick abs" style="left:490px">Some Quick Links<br>Some Quick Links<br>Some Quick Links<br>Some Quick Links<br>Some Quick Links</div>
  <div class="foot-rule abs" style="left:695px"></div>
  <div class="foot-col quick abs" style="left:728px">Some Quick Links<br>Some Quick Links<br>Some Quick Links<br>Some Quick Links<br>Some Quick Links</div>
  <div class="foot-rule abs" style="left:924px"></div>
  <div class="follow abs">Follow us</div>
  <span class="social abs" style="left:960px"></span>
  <span class="social abs" style="left:998px"></span>
  <div class="foot-search abs">Search<i></i></div>
  <p class="copyright abs">Copyright ©201 Torvell Biologics</p>
</footer>

</body>
</html>
```